I have a logo and need to design the business card and stationery.
Updates

The uploaded logo image named as GREYMARSH CONSTRUCTION which is to be replaced to GREYMARSH CONTRACTS. Kindly add below details and submit the designs- Company name- Greymarsh Engineering Contracts LLP Name & Post- Kelvan Joshi (Designated Partner) Address- Block No.317, Wing C, Tulvo Trade Court, Manek Pural Road, Ruparel Industrial Estate, Goregaon(E), Mumbai - 400 063 Contact- +91 97415 60382 Email- kelvanjoshi@mailbrook.example Website- www.greymarshcontracts.example Contact for Letterhead- +91-22-28754193

Hi Tovin Rahul, We are liking your Design #28860835. We have suggested some changes which are mentioned in feedback. Kindly revert with it asap to finalize this design.

Colors

Designer to choose colors to be used in the design.

```html
<!DOCTYPE html>
<html lang="en">
<head>
<meta charset="utf-8">
<title>Greymarsh Contracts – Stationery</title>
<link href="https://fonts.googleapis.com/css2?family=Roboto:wght@400;500;700&family=Montserrat:wght@400;500&family=Oswald:wght@500&display=swap" rel="stylesheet">
<style>
  :root{
    --backdrop:#4b4b4b;
    --band:#333333;
    --paper:#ffffff;
    --ink:#222222;
    --body-ink:#6a6a6a;
    --band-text:#ffffff;
    --card-dark:#2f2f2f;
    --mark-dark:#1c1c1c;
    --tagline-on-band:#1f1f1f;
  }
  *{margin:0;padding:0;box-sizing:border-box}
  html,body{width:1200px;height:1143px;overflow:hidden;background:var(--backdrop)}
  .canvas{position:relative;width:1200px;height:1143px}

  /* Letterhead */
  .letterhead{position:absolute;left:122px;top:238px;width:474px;height:666px;background:var(--paper);box-shadow:0 6px 14px rgba(0,0,0,.45)}
  .letterhead__header{position:absolute;left:0;top:0;width:100%;height:93px;background:var(--band)}
  .brand{position:absolute;display:flex;align-items:center;gap:6px;font-family:'Roboto',sans-serif;font-weight:700;color:var(--band-text);line-height:1.05;letter-spacing:.06em}
  .brand__square{width:14px;height:14px;background:var(--band-text);flex:none}
  .letterhead .brand{left:30px;top:30px;font-size:11px}
  .contact{position:absolute;font-family:'Roboto',sans-serif;color:var(--band-text)}
  .letterhead .contact{left:301px;top:11px;font-size:7.4px;line-height:8.6px}
  .contact__list{list-style:none;margin-top:3px}
  .contact__list li{display:flex;align-items:center;gap:3px;height:10.3px}
  .icon{flex:none}
  .letterhead__body{position:absolute;left:30px;top:174px;width:413px;font-family:'Montserrat',sans-serif;color:var(--body-ink)}
  .salutation{font-size:9.6px;font-weight:500;margin-bottom:24px;color:#555}
  .letterhead__body p{font-size:7.15px;line-height:12.9px;text-align:justify;hyphens:auto;-webkit-hyphens:auto;margin-bottom:14px}
  .signoff__name{font-size:10.2px;font-weight:500;color:#444;line-height:12px}
  .signoff__role{font-size:7px;color:#555}
  .signature{display:block;width:120px;height:38px;margin-top:19px;background:linear-gradient(90deg,#e9e9e9,#f4f4f4);border-radius:2px}
  .letterhead__footer{position:absolute;left:0;bottom:0;width:100%;height:23px;background:var(--band);font-family:'Roboto',sans-serif;font-size:11px;color:var(--tagline-on-band);text-align:center;line-height:23px}

  /* Business cards */
  .card{position:absolute;left:684px;width:395px;height:225px;box-shadow:0 6px 14px rgba(0,0,0,.45)}
  .card--front{top:311px;background:var(--paper)}
  .card--back{top:606px;background:var(--card-dark)}
  .person{position:absolute;right:236px;top:95px;text-align:center}
  .person__name{font-family:'Oswald',sans-serif;font-weight:500;font-size:23px;line-height:26px;letter-spacing:.03em;color:var(--ink)}
  .person__role{font-family:'Roboto',sans-serif;font-size:10.3px;letter-spacing:.05em;color:var(--ink);line-height:11px}
  .card__divider{position:absolute;left:173px;top:72px;width:1px;height:87px;background:#444}
  .card--front .contact{left:189px;top:70px;font-size:9.2px;line-height:11.9px;color:var(--ink);letter-spacing:.02em}
  .card--front .contact__list{margin-top:4px}
  .card--front .contact__list li{height:13px;gap:4px;font-size:9.6px}
  .card--back .brand{left:50%;top:56px;transform:translateX(-50%);flex-direction:column;gap:12px;color:var(--mark-dark);font-size:19px;text-align:center;letter-spacing:.08em}
  .card--back .brand__square{width:40px;height:40px;background:var(--mark-dark)}
  .tagline{position:absolute;left:0;width:100%;top:196px;text-align:center;font-family:'Roboto',sans-serif;font-size:12.4px;color:#151515;letter-spacing:.02em}
</style>
</head>
<body>
<main class="canvas">

  <section class="letterhead">
    <header class="letterhead__header">
      <div class="brand"><span class="brand__square"></span><span>GREYMARSH<br>CONTRACTS</span></div>
      <address class="contact" style="font-style:normal">
        Block No.317, Wing C, Tulvo Trade Court,<br>
        Manek Pural Road,<br>
        Ruparel Industrial Estate, Goregaon(E),<br>
        Mumbai - 400 063 MH, India
        <ul class="contact__list">
          <li><svg class="icon" width="6" height="6" viewBox="0 0 10 10"><path d="M2 1l2 2-1 1.5c.6 1.2 1.3 1.9 2.5 2.5L7 6l2 2-1.3 1.3C4.5 9 1 5.5.7 2.3z" fill="currentColor"/></svg>+91-22-28754193</li>
          <li><svg class="icon" width="6" height="6" viewBox="0 0 10 10"><rect x=".7" y="2" width="8.6" height="6" fill="none" stroke="currentColor"/><path d="M.7 2l4.3 3.3L9.3 2" fill="none" stroke="currentColor"/></svg>kelvan@greymarshcontracts.example</li>
          <li><svg class="icon" width="6" height="6" viewBox="0 0 10 10"><circle cx="5" cy="5" r="4.3" fill="none" stroke="currentColor"/><path d="M.7 5h8.6M5 .7c-2.3 2.6-2.3 6 0 8.6M5 .7c2.3 2.6 2.3 6 0 8.6" fill="none" stroke="currentColor" stroke-width=".7"/></svg>www.greymarshcontracts.example</li>
        </ul>
      </address>
    </header>

    <article class="letterhead__body">
      <p class="salutation">Dear sir/Madam,</p>
      <p>Lorem Ipsum is simply dummy text of the printing and typesetting industry. Lorem Ipsum has been the industry's standard dummy text ever since the 1500s, when an unknown printer took a galley of type and scrambled it to make a type specimen book. It has survived not only five centuries, but also the leap into electronic typesetting, remaining essentially unchanged. It was popularised in the 1960s with the release of Typeline</p>
      <p>Contrary to popular belief, Lorem Ipsum is not simply random text. It has roots in a piece of classical Latin literature from 45 BC, making it over 2000 years old. Edwin Carrow, a Latin professor at Harlow Brook College in Vermont, looked up one of the more obscure Latin words, consectetur, from a Lorem Ipsum passage, and going through the cites of the word in classical literature, discovered the undoubtable source. Lorem Ipsum comes from sections 1.10.32 and 1.10.33 of "de Finibus Bonorum et Malorum" (The Extremes of Good and Evil) by Varronis, written in 45 BC. This book is a treatise on the theory of ethics, very popular during the Renaissance. The first line of Lorem Ipsum, "Lorem ipsum dolor sit amet..", comes from a line in section 1.10.32. typesetting, remaining essentially unchanged. It was popularised in the 1960s with the release of Typeline</p>
      <p>Lorem Ipsum is simply dummy text of the printing and typesetting industry. Lorem Ipsum has been the industry's standard dummy text ever since the 1500s, when an unknown printer took a galley of type and scrambled it to make a type specimen book. It has survived not only five centuries, but also the leap into electronic typesetting, remaining essentially unchanged. It was popularised in the 1960s with the release of Typeline</p>
      <div class="signoff">
        <div class="signoff__name">Marten R. Halden, Esq.</div>
        <div class="signoff__role">Managing Attorney</div>
        <span class="signature" role="img" aria-label="Handwritten signature"></span>
      </div>
    </article>

    <footer class="letterhead__footer">Built on Sound Ground</footer>
  </section>

  <section class="card card--front">
    <div class="person">
      <div class="person__name">KELVAN JOSHI</div>
      <div class="person__role">DESIGNATED PARTNER</div>
    </div>
    <span class="card__divider"></span>
    <address class="contact" style="font-style:normal">
      Block No.317, Wing C, Tulvo Trade Court,<br>
      Manek Pural Road,<br>
      Ruparel Industrial Estate, Goregaon(E),<br>
      Mumbai - 400 063 MH, India
      <ul class="contact__list">
        <li><svg class="icon" width="7" height="7" viewBox="0 0 10 10"><path d="M2 1l2 2-1 1.5c.6 1.2 1.3 1.9 2.5 2.5L7 6l2 2-1.3 1.3C4.5 9 1 5.5.7 2.3z" fill="currentColor"/></svg>+91 97415 60382</li>
        <li><svg class="icon" width="7" height="7" viewBox="0 0 10 10"><rect x=".7" y="2" width="8.6" height="6" fill="none" stroke="currentColor"/><path d="M.7 2l4.3 3.3L9.3 2" fill="none" stroke="currentColor"/></svg>kelvanjoshi@mailbrook.example</li>
        <li><svg class="icon" width="7" height="7" viewBox="0 0 10 10"><circle cx="5" cy="5" r="4.3" fill="none" stroke="currentColor"/><path d="M.7 5h8.6M5 .7c-2.3 2.6-2.3 6 0 8.6M5 .7c2.3 2.6 2.3 6 0 8.6" fill="none" stroke="currentColor" stroke-width=".7"/></svg>www.greymarshcontracts.example</li>
      </ul>
    </address>
  </section>

  <section class="card card--back">
    <div class="brand"><span class="brand__square"></span><span>GREYMARSH<br>CONTRACTS</span></div>
    <p class="tagline">Built on Sound Ground</p>
  </section>

</main>
</body>
</html>
```